Stylish business cards for KV7

To create an appealing and professional business card design for a WOMEN Owned Construction Supply Company.
2 sided card. Incorporate brand elements, curvy, colorful, sleek and bright. No solid white background. attached samples of styles added shapes/ribbons. Want something with that WOW that looks awesome, factor. It is a new logo, so feel free to mess with logo colors in the blue and teal factors that can look good with both dark and light background. If you want to try a watermark with just the KV7, without the "Supply" that might look cool to.

Industry/Entity Type

Women owned construction supply company

Contact Information for Business Card

Name, Title, and phone number and email, web page. maybe spot for qr code.

Font styles to use
Sans Serif

Requirements
Nice to have
• would love to see colors, maybe stylish ribbon dividers or some sort of 2 or 3 tone color card that compliments logo.
Should not have
• Please do not have all white background. Do not include Home/reale state/ or building images.

```html
<!DOCTYPE html>
<html lang="en">
<head>
<meta charset="utf-8">
<title>KV7 Supply – Business Card</title>
<link rel="stylesheet" href="https://fonts.googleapis.com/css2?family=Montserrat:wght@400;500;600;700&display=swap">
<style>
  :root {
    --stage: #1a1a1c;
    --navy: #1b3656;
    --teal: #2393bb;
    --paper: #f3f3f3;
    --white: #ffffff;
    --card-w: 690px;
    --card-h: 392px;
    --radius: 22px;
  }
  * { margin: 0; padding: 0; box-sizing: border-box; }
  html, body {
    width: 1200px;
    height: 1059px;
    overflow: hidden;
    background: var(--stage);
    font-family: "Montserrat", Arial, sans-serif;
  }
  .card {
    position: absolute;
    left: 255px;
    width: var(--card-w);
    height: var(--card-h);
    border-radius: var(--radius);
    overflow: hidden;
  }
  .card--front { top: 89px; background: var(--paper); }
  .card--back { top: 547px; background: var(--navy); }

  .front-shape { position: absolute; inset: 0; width: 100%; height: 100%; }

  .accent-bar {
    position: absolute;
    left: 0; top: 49px;
    width: 18px; height: 35px;
    background: var(--teal);
  }
  .holder {
    position: absolute;
    left: 35px; top: 46px;
    color: var(--white);
  }
  .holder__name {
    font-size: 22px;
    font-weight: 700;
    color: var(--teal);
    letter-spacing: 0.2px;
    line-height: 1;
  }
  .holder__title {
    font-size: 15px;
    font-weight: 400;
    margin-top: 6px;
  }
  .address {
    position: absolute;
    left: 35px; top: 210px;
    color: var(--white);
    font-size: 15px;
    line-height: 22px;
    font-style: normal;
  }
  .contacts {
    position: absolute;
    left: 35px; top: 272px;
    list-style: none;
    color: var(--white);
    font-size: 15px;
  }
  .contacts li {
    display: flex;
    align-items: center;
    height: 28px;
  }
  .contacts svg {
    width: 12px; height: 12px;
    margin-right: 7px;
    flex: none;
  }
  .brand {
    position: absolute;
    font-weight: 600;
    white-space: nowrap;
    display: flex;
    align-items: center;
  }
  .brand--front {
    left: 430px; top: 252px;
    font-size: 36px;
    color: var(--navy);
  }
  .brand--back {
    left: 50%; top: 50%;
    transform: translate(-50%, -50%);
    font-size: 56px;
    color: var(--white);
  }
  .brand__dot {
    display: inline-block;
    border-radius: 50%;
    background: var(--teal);
    margin-right: 12px;
  }
  .brand--front .brand__dot { width: 14px; height: 14px; }
  .brand--back .brand__dot { width: 20px; height: 20px; margin-right: 16px; }
</style>
</head>
<body>

<section class="card card--front" aria-label="Business card front">
  <svg class="front-shape" viewBox="0 0 690 392" preserveAspectRatio="none" aria-hidden="true">
    <path d="M0 0 H338 C392 40 404 110 388 180 C374 240 350 280 352 320 C354 350 370 372 400 392 H0 Z" fill="var(--teal)"/>
    <path d="M0 0 H322 C376 40 386 110 372 180 C358 240 336 280 340 320 C342 350 356 372 384 392 H0 Z" fill="var(--navy)"/>
    <path d="M338 0 C392 40 404 110 388 180" stroke="var(--navy)" stroke-width="8" fill="none"/>
  </svg>

  <span class="accent-bar"></span>
  <header class="holder">
    <h1 class="holder__name">DANA WHITFIELD</h1>
    <p class="holder__title">CEO/Founder</p>
  </header>

  <address class="address">
    P.O Box 3017 Harbour Road<br>
    Fairview AB 40412
  </address>

  <ul class="contacts">
    <li>
      <svg viewBox="0 0 24 24" aria-hidden="true"><path fill="var(--teal)" d="M6.6 10.8a15.1 15.1 0 0 0 6.6 6.6l2.2-2.2a1 1 0 0 1 1-.25 11.4 11.4 0 0 0 3.6.57 1 1 0 0 1 1 1V20a1 1 0 0 1-1 1A17 17 0 0 1 3 4a1 1 0 0 1 1-1h3.5a1 1 0 0 1 1 1c0 1.25.2 2.45.57 3.57a1 1 0 0 1-.25 1z"/></svg>
      555.014.0271
    </li>
    <li>
      <svg viewBox="0 0 24 24" aria-hidden="true"><path fill="var(--teal)" d="M2 5h20v14H2z"/><path d="M2 5l10 8 10-8" stroke="var(--navy)" stroke-width="2" fill="none"/></svg>
      info@kv7supply.com.au
    </li>
    <li>
      <svg viewBox="0 0 24 24" aria-hidden="true"><g fill="none" stroke="var(--teal)" stroke-width="2"><circle cx="12" cy="12" r="10"/><ellipse cx="12" cy="12" rx="4.5" ry="10"/><path d="M2 12h20M4 7h16M4 17h16"/></g></svg>
      www.kv7supply.com.au
    </li>
  </ul>

  <div class="brand brand--front"><span class="brand__dot"></span>KV7 Supply</div>
</section>

<section class="card card--back" aria-label="Business card back">
  <div class="brand brand--back"><span class="brand__dot"></span>KV7 Supply</div>
</section>

</body>
</html>
```